Legal firm website redesign

Existing site for Sydney CBD lawyer needs clean and professional redesign - http://brintonlaw.com.au

The site will be viewed by a wide range of users: businesses, individuals, referral partners and other lawyers.

Please see the list of must haves for further details

Target Market(s)

Businesses, individuals, referral partners and other lawyers

Industry/Entity Type

Lawyer

Requirements
Must have
• Prominent display of phone number.
List of services down the left hand side of the site (5x services or so).
Search box in header.
Please use the greys and blues from the existing header.
New header must include the wording "Efficiency - Fulfillment - Integrity - Teamwork"

```html
<!DOCTYPE html>
<html lang="en">
<head>
<meta charset="utf-8">
<title>Brinton Law</title>
<link href="https://fonts.googleapis.com/css2?family=Arimo:wght@400;700&display=swap" rel="stylesheet">
<style>
:root{
  --grey-dark:#4d4d4d;
  --blue-deep:#1b4f86;
  --blue-band:#2a64a0;
  --blue-bright:#1ea7e1;
  --blue-service:#1479c0;
  --navy-text:#143a64;
  --link:#1e9fd8;
  --page:#e9e9e9;
  --text:#444;
  --footer:#143a6c;
}
*{margin:0;padding:0;box-sizing:border-box}
html,body{width:890px;height:1200px;overflow:hidden}
body{font-family:"Arimo",Arial,sans-serif;background:var(--page);position:relative;color:var(--text)}
.abs{position:absolute}
.topbar{left:0;top:0;width:890px;height:85px;background:linear-gradient(#6e6e6e,var(--grey-dark));border-bottom:1px solid #333}
.brand{left:36px;top:18px;display:flex;align-items:center;gap:14px;color:#fff;font-weight:700;font-size:34px;letter-spacing:-.5px}
.brand-dot{width:44px;height:44px;border-radius:50%;background:#c88a2a}
.phones{right:34px;top:8px;color:#fff;font-size:13px;line-height:31px}
.phones b{color:var(--blue-bright);font-weight:400;font-size:16px;margin-left:6px}
.band{left:0;top:86px;width:890px;height:404px;background:linear-gradient(180deg,var(--blue-deep),var(--blue-band) 60%,#2f6aa8)}
.nav{left:42px;top:100px;width:811px;height:41px;background:linear-gradient(#fff,#e9e9e9);display:flex;align-items:center;padding-left:11px}
.nav a{font-size:12px;color:#222;text-decoration:none;padding:9px 11px}
.nav a.active{background:var(--blue-bright);color:#fff;border-radius:2px;padding:9px 13px}
.search{position:absolute;right:11px;top:11px;width:176px;height:22px;border:1px solid #bbb;border-radius:3px;background:#fff}
.search span{position:absolute;right:0;top:0;width:25px;height:20px;border-left:1px solid #bbb;background:#eee}
.stage{left:42px;top:153px;width:811px;height:321px;background:#fff;box-shadow:0 8px 10px rgba(0,0,0,.35)}
.services{left:51px;top:162px;width:288px;height:305px;background:linear-gradient(var(--blue-bright),var(--blue-service))}
.services h2{color:#fff;font-size:16px;position:absolute;left:26px;top:18px}
.services ul{list-style:none;position:absolute;left:26px;top:54px;width:250px}
.services li{color:#fff;font-size:11.5px;line-height:16px;padding-left:18px;position:relative;margin-bottom:10px}
.services li::before{content:"";position:absolute;left:0;top:4px;width:8px;height:8px;border-radius:50%;background:#fff}
.hero{left:355px;top:166px;width:485px;height:299px;background:linear-gradient(135deg,#e4e0da,#9a7b63 45%,#3d3b3c 80%)}
.values{left:683px;top:281px;color:#fff;font-weight:700;font-size:18px;line-height:42px;text-shadow:0 0 2px #000}
.values li{list-style:none}
.values li::before{content:"▸ ";color:var(--blue-bright);font-size:12px}
.arrow{width:38px;height:32px;background:var(--blue-bright);color:#fff;font-size:22px;text-align:center;line-height:30px}
.panel{background:#fff;border-radius:3px}
.heading{background:#eee;border-radius:3px;color:var(--navy-text);font-size:16px;padding:9px 9px}
.about{left:43px;top:511px;width:567px;height:620px}
.about-photo{left:66px;top:572px;width:168px;height:210px;background:linear-gradient(#e6e6e6,#5a6d8c);border:1px solid #ccc}
.about-text{left:253px;top:573px;width:356px;font-size:11.4px;line-height:18px}
.about-text p{margin-bottom:18px}
.rule{left:56px;top:800px;width:535px;border-top:1px dotted #999}
.additions{left:76px;top:847px;font-size:11.5px;line-height:21px;list-style:none}
.additions li:first-child{color:var(--link)}
.side-h{color:#1877b8;font-size:13px;display:flex;align-items:center;gap:12px;padding:8px}
.side-h i{width:24px;height:24px;display:block;border-radius:3px}
.field{border:1px solid #bbb;border-radius:4px;height:26px;width:136px;font-size:10px;padding:7px 15px;color:#333;position:absolute;left:641px}
.btn{left:788px;top:607px;width:58px;height:25px;background:var(--blue-bright);color:#fff;font-size:11px;text-align:center;line-height:25px;border-radius:2px}
.date{width:52px;height:50px;background:linear-gradient(var(--blue-bright),var(--blue-service));color:#fff;font-size:11.5px;line-height:14px;padding:11px 8px}
.news{font-size:9px;line-height:12px;color:#555;width:125px}
.contact{left:651px;top:953px;font-size:12px;line-height:18.3px;color:#333;font-style:normal}
.footer{left:0;top:1121px;width:890px;height:79px;background:var(--footer)}
.social{left:67px;top:1150px;display:flex;gap:5px}
.social i{width:23px;height:23px;border-radius:3px;background:#3a7fd0;display:block}
.social i:last-child{background:#e57a2a}
.foot-nav{right:45px;top:1152px;color:#fff;font-size:11px}
.foot-nav span{margin:0 7px}
.copy{left:478px;top:1177px;color:#fff;font-size:11px}
</style>
</head>
<body>
<div class="abs topbar"></div>
<div class="abs brand"><span class="brand-dot"></span>brinton law</div>
<div class="abs phones">TELEPHONE :<b>(02) 9000 4120</b><br>FACSIMILE :<b>(02) 9000 4130</b></div>

<div class="abs band"></div>
<nav class="abs nav">
  <a class="active">HOME</a><a>ABOUT US</a><a>AREAS OF LAW</a><a>PUBLICATIONS</a><a>CONTACT</a>
  <div class="search"><span></span></div>
</nav>
<div class="abs stage"></div>
<section class="abs services">
  <h2>OUR SERVICES</h2>
  <ul>
    <li>BUYING AND SELLING BUSINESSES AND COMPANIES</li>
    <li>FINANCING</li>
    <li>LEASING</li>
    <li>PROPERTY TRANSACTIONS</li>
    <li>JOINT VENTURES</li>
    <li>BUSINESS RESTRUCTURING</li>
    <li>CONTRACT REVIEW AND ADVICE</li>
    <li style="margin-top:14px">EMPLOYMENT LAW DOCUMENTATION, E.G. AWAS</li>
  </ul>
</section>
<div class="abs hero" role="img" aria-label="Photo of four smiling lawyers in suits with a gavel behind them"></div>
<ul class="abs values"><li>EFFICIENCY</li><li>FULFILLMENT</li><li>INTEGRITY</li><li>TEAMWORK</li></ul>
<div class="abs arrow" style="left:347px;top:289px">«</div>
<div class="abs arrow" style="left:813px;top:289px">»</div>

<section class="abs panel about"></section>
<div class="abs heading" style="left:53px;top:521px;width:214px">ABOUT BRINTON LAW</div>
<div class="abs about-photo" role="img" aria-label="Photo of three professionals holding scales of justice"></div>
<div class="abs about-text">
  <p>Brinton Law is a dynamic commercial law firm in the CBD of Sydney providing services to corporate, small business and private clients.</p>
  <p>Brinton Law brings together over 30 years of experience in legal practice.</p>
  <p>The strong focus of the firm is on commercial law and estate planning.</p>
  <p>Brinton Law is committed to providing quality legal services in helping its clients achieve their objectives by providing a proactive understanding of its clients' businesses and creative legal solutions.</p>
</div>
<div class="abs rule"></div>
<div class="abs heading" style="left:60px;top:811px;width:214px;font-size:14px">RECENT ADDITIONS</div>
<ul class="abs additions">
  <li>Commencement of the Succession Act 2006 25.03.08</li>
  <li>Is that will valid? 15.01.08</li>
  <li>Labor's proposed changes to IR laws 14.12.07</li>
  <li>Should you make your own will? 14.11.07</li>
  <li>Illegal workers 14.08.07</li>
  <li>Employees' liability for misleading or deceptive conduct 14.08.07</li>
  <li>Correct use of ACNs and ABNs 14.08.07</li>
  <li>Power of Attorney Infosheet 10.08.07</li>
  <li>Intestate Estates Infosheet 08.08.07</li>
  <li>Estate Planning Infosheet 07.06.07</li>
  <li>Special Disability Trusts Infosheet 18.05.07</li>
  <li>Testamentary Trusts Infosheet 17.05.07</li>
  <li>Appointment of an Enduring Guardian Infosheet 15.05.07</li>
</ul>

<section class="abs panel" style="left:626px;top:511px;width:226px;height:139px"></section>
<div class="abs heading side-h" style="left:633px;top:516px;width:214px"><i style="background:#8a2a2a;border-radius:50%"></i>LOGIN</div>
<div class="field" style="top:568px">User Name</div>
<div class="field" style="top:606px">Password</div>
<div class="abs btn">LOGIN</div>

<section class="abs panel" style="left:626px;top:660px;width:226px;height:235px"></section>
<div class="abs heading side-h" style="left:633px;top:664px;width:214px"><i style="background:#bbb"></i>RECENT NEWS</div>
<div class="abs date" style="left:640px;top:724px">Mar 3,<br>2012</div>
<div class="abs news" style="left:704px;top:729px">Nunc varius facilisis eros. Sed erat. In in velit quis arcu ornare laoreet. luctus massa.</div>
<div class="abs date" style="left:640px;top:812px">Mar 3,<br>2012</div>
<div class="abs news" style="left:704px;top:816px">Nunc varius facilisis eros. Sed erat. In in velit quis arcu ornare laoreet. luctus massa.</div>
<div class="abs" style="left:786px;top:874px;font-size:10px;color:#1877b8">More News</div>

<section class="abs panel" style="left:626px;top:905px;width:226px;height:227px"></section>
<div class="abs heading side-h" style="left:633px;top:908px;width:214px"><i style="background:#e8a830"></i>CONTACT</div>
<address class="abs contact">
  Brinton Law Pty Ltd<br>Level 4, 12 Harbour Lane<br>Sydney NSW 2000<br>Telephone: (02) 9000 4120<br>Facsimile:&nbsp;&nbsp; (02) 9000 4130<br>Email : info@brintonlaw.com.au<br><br>GPO Box 318<br>Sydney NSW 2001
</address>

<footer class="abs footer"></footer>
<div class="abs social"><i></i><i></i><i></i><i></i></div>
<div class="abs foot-nav">Home<span>|</span>About Us<span>|</span>Area of Law<span>|</span>Our People<span>|</span>Publication<span>|</span>Contact</div>
<div class="abs copy">Copyright 2012 brintonlaw, All Rights Reserved</div>
</body>
</html>
```